I need a business card design for a new business based in South West Australia.
I specialize in residential window cleaning & general handyman maintenance.

Dale Marsh - 412 SILVER HAWK DETAILING
- Window Cleaning
- House Maintenance

```html
<!DOCTYPE html>
<html lang="en">
<head>
<meta charset="utf-8">
<title>412 Silver Hawk Detailing – Business Card</title>
<link rel="stylesheet" href="https://fonts.googleapis.com/css2?family=Arimo:wght@400;700&family=Tinos:wght@700&display=swap">
<style>
  :root {
    --page-bg: #d8d1c6;
    --blue-deep: #1d3f73;
    --blue-mid: #2a5b9a;
    --blue-light: #3d6aa6;
    --frost-light: #f1f3f4;
    --frost-mid: #d9dee3;
    --swoosh: #1e1f22;
    --silver: #c9c4bd;
    --ink: #111214;
    --service-tan: #c9b49a;
    --name-tan: #d9c2a6;
    --name-rose: #c98a86;
    --icon-rose: #d88c8c;
    --tool-dark: #2b2d31;
    --tool-grey: #8d9095;
  }
  * { margin: 0; padding: 0; box-sizing: border-box; }
  html, body {
    width: 1200px;
    height: 970px;
    overflow: hidden;
    background: var(--page-bg);
  }
  .business-card {
    position: absolute;
    left: 65px;
    top: 166px;
    width: 1070px;
    height: 638px;
    overflow: hidden;
    box-shadow: 0 10px 30px rgba(0,0,0,0.18);
  }
  .card-art {
    position: absolute;
    inset: 0;
    width: 100%;
    height: 100%;
    display: block;
  }
  .company-name {
    position: absolute;
    left: 0;
    top: 122px;
    width: 1104px;
    text-align: center;
    font-family: "Arimo", Arial, sans-serif;
    font-weight: 700;
    font-size: 50px;
    letter-spacing: 0.5px;
    color: var(--ink);
  }
  .owner-name {
    position: absolute;
    left: 64px;
    top: 520px;
    font-family: "Tinos", "Times New Roman", serif;
    font-weight: 700;
    font-size: 66px;
    background: linear-gradient(90deg, var(--name-tan) 0%, var(--name-rose) 100%);
    -webkit-background-clip: text;
    background-clip: text;
    color: transparent;
  }
  .services {
    position: absolute;
    left: 560px;
    top: 496px;
    list-style: none;
  }
  .service {
    display: flex;
    align-items: center;
    height: 74px;
    font-family: "Arimo", Arial, sans-serif;
    font-size: 39px;
    color: var(--service-tan);
  }
  .service-icon {
    width: 32px;
    height: 32px;
    margin-right: 34px;
    flex: none;
  }
</style>
</head>
<body>
  <div class="business-card">
    <svg class="card-art" viewBox="0 0 1070 638" xmlns="http://www.w3.org/2000/svg">
      <defs>
        <linearGradient id="blueField" x1="0" y1="0" x2="0.3" y2="1">
          <stop offset="0" stop-color="var(--blue-light)"/>
          <stop offset="0.55" stop-color="var(--blue-mid)"/>
          <stop offset="1" stop-color="var(--blue-deep)"/>
        </linearGradient>
        <linearGradient id="frostField" x1="0" y1="0" x2="0" y2="1">
          <stop offset="0" stop-color="var(--frost-mid)"/>
          <stop offset="0.5" stop-color="var(--frost-light)"/>
          <stop offset="1" stop-color="var(--frost-mid)"/>
        </linearGradient>
        <linearGradient id="toolTone" x1="0" y1="0" x2="1" y2="1">
          <stop offset="0" stop-color="var(--tool-grey)"/>
          <stop offset="1" stop-color="var(--tool-dark)"/>
        </linearGradient>
      </defs>

      <rect class="blue-field" width="1070" height="638" fill="url(#blueField)"/>
      <path class="frost-arc" d="M0,0 H1070 V112 C1000,320 820,468 560,470 C300,472 90,340 0,118 Z" fill="url(#frostField)"/>
      <path class="silver-line" d="M0,150 C80,340 300,478 560,480 C680,481 760,455 810,420" fill="none" stroke="var(--silver)" stroke-width="3"/>
      <path class="black-swoosh" d="M0,100 C50,300 260,452 560,458 C680,460 770,430 820,372 C760,444 660,470 560,470 C290,470 70,340 0,142 Z" fill="var(--swoosh)"/>

      <rect class="squeegee-placeholder" role="img" aria-label="Window cleaning squeegee illustration" x="640" y="218" width="310" height="232" rx="6" fill="url(#toolTone)" opacity="0.55"/>
    </svg>

    <div class="company-name">412 SILVER HAWK DETAILING</div>
    <div class="owner-name">Dale Marsh</div>

    <ul class="services">
      <li class="service">
        <svg class="service-icon" viewBox="0 0 32 32" aria-hidden="true">
          <circle cx="16" cy="16" r="10" fill="none" stroke="var(--icon-rose)" stroke-width="2"/>
          <circle cx="16" cy="16" r="4" fill="var(--icon-rose)"/>
          <path d="M16 1V9M16 23V31M1 16H9M23 16H31" stroke="var(--icon-rose)" stroke-width="2"/>
        </svg>
        Window Cleaning
      </li>
      <li class="service">
        <svg class="service-icon" viewBox="0 0 32 32" aria-hidden="true">
          <circle cx="16" cy="16" r="10" fill="none" stroke="var(--icon-rose)" stroke-width="2"/>
          <circle cx="16" cy="16" r="4" fill="var(--icon-rose)"/>
          <path d="M16 1V9M16 23V31M1 16H9M23 16H31" stroke="var(--icon-rose)" stroke-width="2"/>
        </svg>
        House Maintenance
      </li>
    </ul>
  </div>
</body>
</html>
```